Pet Care Business Card

Dog & Cat Grooming, we come to you or come to Whisker Haven Grooming
Doggy day care,
Boutique holiday care,
Pet Supplies
All Natural Products used
Have created the logo, which I will forward shortly but need help to have it on flyers business cards ect
email whiskerhavengrooming@mailbrook.net
Ph: 0471352706
Colours: Green Black and paws prints nott sure what colour for them
Updates
Thank you to all that forwarded their designs, very hard choice and I thank you for your effort, shall recommend this to all my collegues
Thanks Again Dot :)
Industry/Entity Type
Business
Contact Information for Business Card
0471352706
517 upper Tindale Road
Brookvale QLD 4581

```html
<!DOCTYPE html>
<html lang="en">
<head>
<meta charset="utf-8">
<title>Whisker Haven Grooming – Business Card</title>
<link rel="stylesheet" href="https://fonts.googleapis.com/css2?family=Open+Sans:wght@400;600;700&display=swap">
<style>
  :root {
    --bg: #e9e6e1;
    --card-white: #ffffff;
    --brand-blue: #1673d0;
    --stripe-dark: #3a3a3c;
    --ink: #2b2b2b;
    --ink-soft: #4a4a4a;
    --on-blue: #ffffff;
  }
  * { box-sizing: border-box; margin: 0; padding: 0; }
  html, body {
    width: 1200px; height: 865px; overflow: hidden;
    background: var(--bg);
    font-family: "Open Sans", Arial, sans-serif;
  }
  .stage {
    width: 1200px; height: 865px;
    display: flex; flex-direction: column;
    align-items: center; justify-content: center; gap: 40px;
  }
  .card {
    position: relative;
    width: 640px; height: 366px;
    box-shadow: 0 6px 18px rgba(0,0,0,.18);
    overflow: hidden;
  }

  /* Front */
  .card--front { background: var(--brand-blue); }
  .front-top {
    position: absolute; left: 0; top: 0; right: 0; height: 200px;
    background: var(--card-white);
  }
  .front-divider {
    position: absolute; left: 0; right: 0; top: 200px; height: 12px;
    background: var(--stripe-dark);
  }
  .brand {
    position: absolute; left: 44px; top: 46px;
    display: flex; align-items: center; gap: 12px;
  }
  .brand-dot {
    width: 16px; height: 16px; border-radius: 50%;
    background: var(--brand-blue);
  }
  .brand-name {
    font-weight: 600; font-size: 27px; line-height: 1.15;
    color: var(--brand-blue); letter-spacing: .5px;
  }
  .person {
    position: absolute; right: 34px; top: 30px; text-align: right;
  }
  .person-name {
    font-weight: 700; font-size: 19px; color: var(--ink);
    letter-spacing: .5px; text-transform: uppercase;
  }
  .person-title { font-size: 14px; color: var(--ink-soft); margin-top: 2px; }
  .address {
    position: absolute; left: 44px; top: 132px;
    display: flex; align-items: center; gap: 12px;
    font-size: 15px; line-height: 1.35; color: var(--ink);
  }
  .icon { flex: none; }
  .contacts {
    position: absolute; left: 44px; right: 34px; top: 240px;
    display: grid; grid-template-columns: 1fr 1.35fr; row-gap: 22px; column-gap: 20px;
  }
  .contact {
    display: flex; align-items: center; gap: 10px;
    color: var(--on-blue); font-weight: 600; font-size: 14px;
    white-space: nowrap;
  }

  /* Back */
  .card--back { background: var(--brand-blue); }
  .back-stripe {
    position: absolute; top: 0; bottom: 0; left: 40px; width: 14px;
    background: var(--stripe-dark);
  }
</style>
</head>
<body>
<main class="stage">
  <section class="card card--front" aria-label="Business card front">
    <div class="front-top"></div>
    <div class="front-divider"></div>

    <div class="brand">
      <span class="brand-dot"></span>
      <span class="brand-name">Whisker Haven<br>Grooming</span>
    </div>

    <div class="person">
      <p class="person-name">Dot Hargreave</p>
      <p class="person-title">Managing Director</p>
    </div>

    <div class="address">
      <svg class="icon" width="16" height="22" viewBox="0 0 16 22" aria-hidden="true">
        <path d="M8 0C3.6 0 0 3.5 0 7.9 0 13.5 8 22 8 22s8-8.5 8-14.1C16 3.5 12.4 0 8 0z" fill="#2b2b2b"/>
        <circle cx="8" cy="8" r="3" fill="#fff"/>
      </svg>
      <p>517 upper Tindale Road<br>Brookvale QLD 4581</p>
    </div>

    <div class="contacts">
      <p class="contact">
        <svg class="icon" width="12" height="16" viewBox="0 0 12 16" aria-hidden="true">
          <rect x="1" y="1" width="10" height="14" rx="1.5" fill="none" stroke="#fff" stroke-width="1.6"/>
          <line x1="4.5" y1="12.5" x2="7.5" y2="12.5" stroke="#fff" stroke-width="1.4"/>
        </svg>
        0471352706
      </p>
      <p class="contact">
        <svg class="icon" width="15" height="15" viewBox="0 0 24 24" aria-hidden="true">
          <path d="M6.6 10.8c1.4 2.8 3.8 5.1 6.6 6.6l2.2-2.2c.3-.3.7-.4 1-.2 1.1.4 2.3.6 3.6.6.6 0 1 .4 1 1V20c0 .6-.4 1-1 1C10.6 21 3 13.4 3 4c0-.6.4-1 1-1h3.5c.6 0 1 .4 1 1 0 1.3.2 2.5.6 3.6.1.3 0 .7-.2 1L6.6 10.8z" fill="#fff"/>
        </svg>
        0471352706
      </p>
      <p class="contact">
        <svg class="icon" width="15" height="15" viewBox="0 0 20 20" aria-hidden="true">
          <circle cx="10" cy="10" r="8.5" fill="none" stroke="#fff" stroke-width="1.5"/>
          <ellipse cx="10" cy="10" rx="3.8" ry="8.5" fill="none" stroke="#fff" stroke-width="1.3"/>
          <line x1="1.5" y1="10" x2="18.5" y2="10" stroke="#fff" stroke-width="1.3"/>
        </svg>
        www.whiskerhavengrooming.net
      </p>
      <p class="contact">
        <svg class="icon" width="16" height="12" viewBox="0 0 16 12" aria-hidden="true">
          <rect x="0" y="0" width="16" height="12" rx="1" fill="#fff"/>
          <path d="M1 1l7 5.5L15 1" fill="none" stroke="#1673d0" stroke-width="1.4"/>
        </svg>
        whiskerhavengrooming@mailbrook.net
      </p>
    </div>
  </section>

  <section class="card card--back" aria-label="Business card back">
    <div class="back-stripe"></div>
  </section>
</main>
</body>
</html>
```